Veldmark Supplies Business Card

Professional business card that stand out to our potential customers. Front and back with clean modern design

Industry/Entity Type

Oil and gas

Contact Information for Business Card

Name, address, website , office phone and cell number

Requirements
Must have
• Editable files for each employee

```html
<!DOCTYPE html>
<html lang="en">
<head>
<meta charset="utf-8">
<title>Veldmark Supplies Business Card</title>
<link rel="stylesheet" href="https://fonts.googleapis.com/css2?family=Montserrat:wght@500;600;700&family=Questrial&display=swap">
<style>
  :root {
    --signal-red: #ff0000;
    --ocean-blue: #03b2cf;
    --ink: #111111;
    --card-black: #000000;
    --paper: #ffffff;
    --backdrop: #ffffff;
  }
  html, body {
    margin: 0;
    width: 1200px;
    height: 1200px;
    overflow: hidden;
    background: var(--backdrop);
  }
  .sheet { display: block; width: 1200px; height: 1200px; }
  .brand-name {
    font-family: "Montserrat", sans-serif;
    font-weight: 700;
    fill: var(--signal-red);
    letter-spacing: 1px;
  }
  .brand-mark { fill: var(--signal-red); }
  .web-line {
    font-family: "Questrial", sans-serif;
    font-size: 19px;
    fill: var(--paper);
    letter-spacing: 0.5px;
  }
  .person-name {
    font-family: "Montserrat", sans-serif;
    font-weight: 600;
    font-size: 38px;
    letter-spacing: 5px;
    fill: var(--ink);
  }
  .person-title {
    font-family: "Montserrat", sans-serif;
    font-weight: 600;
    font-size: 21px;
    fill: var(--ink);
  }
  .contact-text {
    font-family: "Questrial", sans-serif;
    font-size: 18px;
    fill: var(--ink);
    letter-spacing: 0.5px;
  }
  .contact-phone { letter-spacing: 2.5px; }
  .address-text {
    font-family: "Questrial", sans-serif;
    font-size: 18px;
    fill: var(--ink);
  }
  .icon-disc { fill: var(--signal-red); }
  .icon-glyph { fill: none; stroke: var(--paper); stroke-width: 1.4; stroke-linecap: round; stroke-linejoin: round; }
  .divider { stroke: var(--ink); stroke-width: 2; }
  .accent-red { fill: var(--signal-red); }
  .accent-blue { fill: var(--ocean-blue); }
  .card-front { fill: var(--card-black); }
  .card-back { fill: var(--paper); stroke: #e6e6e6; stroke-width: 1; }
</style>
</head>
<body>
<svg class="sheet" viewBox="0 0 1200 1200" xmlns="http://www.w3.org/2000/svg">

  <!-- Front face -->
  <g class="front-face" transform="translate(181 94)">
    <rect class="card-front" width="845" height="482"/>
    <rect class="brand-mark" x="392" y="140" width="60" height="60"/>
    <text class="brand-name" x="422" y="338" font-size="30" text-anchor="middle">VELDMARK SUPPLIES</text>
    <text class="web-line" x="794" y="445" text-anchor="end">www.yourwebsite.com</text>
  </g>

  <!-- Back face -->
  <g class="back-face" transform="translate(181 630)">
    <rect class="card-back" width="845" height="483"/>

    <rect class="accent-red" x="0" y="204" width="15" height="74"/>

    <text class="person-name" x="75" y="242">Your Name</text>
    <text class="person-title" x="75" y="269">Your Title</text>

    <line class="divider" x1="75" y1="294" x2="770" y2="294"/>

    <g class="contact-phone-row" transform="translate(88 331)">
      <circle class="icon-disc" r="13"/>
      <path class="icon-glyph" d="M-6 -6 l3 -1 l2 4 l-2 2 q2 4 6 6 l2 -2 l4 2 l-1 3 q-9 1 -14 -14z"/>
    </g>
    <text class="contact-text contact-phone" x="116" y="337">123-456-789</text>

    <g class="contact-web-row" transform="translate(88 364)">
      <circle class="icon-disc" r="13"/>
      <circle class="icon-glyph" r="7"/>
      <ellipse class="icon-glyph" rx="3" ry="7"/>
      <line class="icon-glyph" x1="-7" y1="0" x2="7" y2="0"/>
    </g>
    <text class="contact-text" x="116" y="370">www.yourwebsite.com</text>

    <g class="contact-mail-row" transform="translate(88 397)">
      <circle class="icon-disc" r="13"/>
      <rect class="icon-glyph" x="-7" y="-5" width="14" height="10"/>
      <path class="icon-glyph" d="M-7 -5 L0 1 L7 -5 M-7 5 L-2 0 M7 5 L2 0"/>
    </g>
    <text class="contact-text" x="116" y="403">email@info.com</text>

    <rect class="brand-mark" x="628" y="98" width="50" height="50"/>
    <text class="brand-name" x="653" y="242" font-size="22" text-anchor="middle">VELDMARK SUPPLIES</text>

    <text class="address-text" x="770" y="402" text-anchor="end">Your Address and Country</text>

    <polygon class="accent-red" points="0,470 517,470 509,483 0,483"/>
    <polygon class="accent-blue" points="546,443 845,443 845,483 521,483"/>
  </g>
</svg>
</body>
</html>
```